Business card design for a dynamic IT consulting company

We need a business card design for a young firm, specialized in the Telecommunications/Consulting industry. The name of the company is Quindor and Partners Business Consulting Ltd. (Short name: Quindor and Partnes)
Quindor = solve read reverse, so we aim to be uncomplicated and solution-oriented. The small pipe in our logo is also related to the word solve. So we need a new business card design, which is simple, eye catching and something non traditional (I would probably prefer a square shaped design rather than a rectangle, but open for suggestions). Attached our logo.

Target Market(s)

Usually our customers are Tier1 Telecoms providers (Q-Netra, Palorix, etc) and their executives.

Industry/Entity Type

Business

Contact Information for Business Card

Name: Bence Tolnavari
Email: b.tolnavari@quindor.hu
Web: www.quindor.hu
Mobile: +36 30 518 2769
Title: Managing Director

Optional:
Company name: Quindor and Partners Ltd.
Address: 1087 Budapest, Tolvenka str. 28/C, Hungary

Font styles to use
Other font styles liked:
• helveticaneue_medium, Prime Regular are used now.

Colors

Designer to choose colors to be used in the design.

Requirements
Must have
• I would like to have a 2 sided design.
Nice to have
• I thought if we make the logo a bit bigger (without the company name), that could go to the back with the company name below. I though, if the pipe in the logo is somehow touchable on the business card, would be nice and unique.

```html
<!DOCTYPE html>
<html lang="en">
<head>
<meta charset="utf-8">
<title>Quindor and Partners – Business Card</title>
<link href="https://fonts.googleapis.com/css2?family=Open+Sans:wght@400;600;700&display=swap" rel="stylesheet">
<style>
  :root {
    --bg: #e9e6e2;
    --card-white: #ffffff;
    --card-black: #050505;
    --ink: #3f3f41;
    --ink-soft: #6d6d70;
    --name-grey: #6a6a6c;
    --name-grey-light: #8c8c8f;
    --cyan: #1aa3e0;
    --magenta: #b8449c;
    --cyan-pale: #a9cdf0;
    --magenta-pale: #dba7d2;
  }
  * { box-sizing: border-box; margin: 0; padding: 0; }
  html, body { width: 1200px; height: 1200px; overflow: hidden; }
  body {
    background: var(--bg);
    font-family: "Open Sans", Arial, sans-serif;
    display: flex;
    flex-direction: column;
    align-items: center;
    justify-content: center;
    gap: 64px;
  }
  .card {
    position: relative;
    width: 900px;
    height: 500px;
    box-shadow: 0 10px 30px rgba(0,0,0,.18);
  }
  .card--back { background: var(--card-black); }
  .card--front { background: var(--card-white); }

  .corner { position: absolute; width: 24px; height: 24px; }
  .corner--tl { top: 28px; left: 28px; }
  .corner--tr { top: 28px; right: 28px; }
  .corner--bl { bottom: 28px; left: 28px; }
  .corner--br { bottom: 28px; right: 28px; }
  .sq-cyan { background: var(--cyan); }
  .sq-magenta { background: var(--magenta); }
  .sq-cyan-pale { background: var(--cyan-pale); }
  .sq-magenta-pale { background: var(--magenta-pale); }

  .company {
    display: flex;
    align-items: center;
    white-space: nowrap;
  }
  .company__square { flex: none; background: var(--magenta); }
  .company__name {
    font-family: "Open Sans", Arial, sans-serif;
    font-weight: 400;
    line-height: 1;
  }

  /* back side */
  .back-company {
    position: absolute;
    left: 50%; top: 50%;
    transform: translate(-50%, -50%);
    gap: 22px;
  }
  .back-company .company__square { width: 34px; height: 34px; }
  .back-company .company__name { font-size: 52px; color: var(--name-grey-light); }

  /* front side */
  .front-company {
    position: absolute;
    left: 110px; top: 78px;
    gap: 26px;
  }
  .front-company .company__square { width: 44px; height: 44px; }
  .front-company .company__name { font-size: 62px; color: var(--name-grey); }

  .person { position: absolute; left: 110px; top: 240px; color: var(--ink); }
  .person__name { font-size: 40px; font-weight: 700; letter-spacing: -.01em; line-height: 1.2; }
  .person__title { font-size: 22px; font-weight: 600; color: var(--ink-soft); margin-top: 4px; }

  .contacts {
    position: absolute;
    left: 110px; right: 90px; bottom: 58px;
    display: flex;
    justify-content: space-between;
    align-items: flex-end;
    font-size: 18px;
    color: var(--ink);
    line-height: 1.4;
  }
  .contact-group { display: flex; flex-direction: column; gap: 6px; }
  .contact-line { display: flex; align-items: flex-start; gap: 12px; }
  .contact-line svg { flex: none; width: 20px; height: 20px; margin-top: 3px; }
</style>
</head>
<body>

  <section class="card card--back" aria-label="Business card, back side">
    <span class="corner corner--tl sq-cyan"></span>
    <span class="corner corner--tr sq-magenta"></span>
    <span class="corner corner--bl sq-magenta"></span>
    <span class="corner corner--br sq-cyan"></span>
    <div class="company back-company">
      <span class="company__square"></span>
      <span class="company__name">Quindor &amp; Partners</span>
    </div>
  </section>

  <section class="card card--front" aria-label="Business card, front side">
    <span class="corner corner--tl sq-magenta-pale"></span>
    <span class="corner corner--tr sq-cyan-pale"></span>
    <span class="corner corner--bl sq-cyan-pale"></span>

    <div class="company front-company">
      <span class="company__square"></span>
      <span class="company__name">Quindor &amp; Partners</span>
    </div>

    <div class="person">
      <div class="person__name">Bence Tolnavari</div>
      <div class="person__title">Managing Director</div>
    </div>

    <div class="contacts">
      <div class="contact-group">
        <div class="contact-line">
          <svg viewBox="0 0 20 20" aria-hidden="true"><path d="M10 1a6 6 0 0 0-6 6c0 4.5 6 12 6 12s6-7.5 6-12a6 6 0 0 0-6-6zm0 8.4A2.4 2.4 0 1 1 10 4.6a2.4 2.4 0 0 1 0 4.8z" fill="var(--cyan)"/></svg>
          <span>1087 Budapest, Tolvenka str.<br>28/C, Hungary</span>
        </div>
        <div class="contact-line">
          <svg viewBox="0 0 20 20" aria-hidden="true"><path d="M5.2 2.5l2.6 3.2-1.6 1.9a10 10 0 0 0 6.2 6.2l1.9-1.6 3.2 2.6-1.8 2.7C9.4 17.1 2.9 10.6 2.5 4.3z" fill="var(--magenta)"/></svg>
          <span>+36 30 518 2769</span>
        </div>
      </div>
      <div class="contact-group">
        <div class="contact-line">
          <svg viewBox="0 0 20 20" aria-hidden="true"><rect x="2" y="4" width="16" height="12" fill="var(--cyan)"/><path d="M2 4l8 7 8-7" fill="none" stroke="#fff" stroke-width="1.6"/></svg>
          <span>b.tolnavari@quindor.hu</span>
        </div>
        <div class="contact-line">
          <svg viewBox="0 0 20 20" aria-hidden="true"><circle cx="10" cy="10" r="8" fill="var(--magenta)"/><path d="M2 10h16M10 2c-3 3-3 13 0 16M10 2c3 3 3 13 0 16" fill="none" stroke="#fff" stroke-width="1.3"/></svg>
          <span>www.quindor.hu</span>
        </div>
      </div>
    </div>
  </section>

</body>
</html>
```